business card for a massage therapy practice named 'Cedar and Willow Massage Studio'

I really need a trendy, yet easy on the eyes business card to complement my logo. Ideally with some gold or rose gold foil work.

My uploaded file of the logo I have in horizontal but I have a vertical version as well. Another color that is used in the website is a blush pink here and there. I'd like to see some trendy tropical leaves in the design.

```html
<!DOCTYPE html>
<html lang="en">
<head>
<meta charset="utf-8">
<title>Cedar &amp; Willow Massage Studio — Business Card</title>
<link rel="stylesheet" href="https://fonts.googleapis.com/css2?family=Dancing+Script:wght@500&family=Open+Sans:wght@400;600&display=swap">
<style>
  :root {
    --page: #f3efec;
    --blush: #f8dcdf;
    --blush-light: #fbe9ea;
    --blush-band: #f6c3c8;
    --wine: #b84a55;
    --wine-deep: #7e2f3b;
    --wine-line: #4a1820;
    --ink: #231a1a;
    --white: #ffffff;
  }
  * { box-sizing: border-box; margin: 0; padding: 0; }
  html, body {
    width: 1200px; height: 1200px; overflow: hidden;
    background: var(--page);
    font-family: "Open Sans", Arial, sans-serif;
  }
  .canvas {
    position: relative; width: 1200px; height: 1200px;
    display: flex; justify-content: center; align-items: center; gap: 60px;
  }
  .card {
    position: relative; width: 440px; height: 770px; overflow: hidden;
    background: linear-gradient(160deg, var(--blush-light), var(--blush));
    box-shadow: 0 14px 34px rgba(60, 30, 30, 0.18);
  }
  .card__wave { position: absolute; inset: 0; width: 100%; height: 100%; }
  .brand {
    position: absolute; display: flex; align-items: center; gap: 12px;
    color: var(--ink); font-weight: 600; font-size: 26px; line-height: 1.2;
  }
  .brand__dot {
    width: 16px; height: 16px; border-radius: 50%;
    background: #b59a62; flex: none;
  }
  .card--front .brand { top: 80px; left: 62px; }
  .card--back .brand { top: 340px; left: 0; right: 0; justify-content: center; text-align: left; }
  .person {
    position: absolute; left: 62px; top: 420px; color: var(--white);
  }
  .person__name {
    font-family: "Dancing Script", cursive; font-weight: 500;
    font-size: 54px; line-height: 1;
  }
  .person__role { font-size: 20px; margin-top: 14px; }
  .contact {
    position: absolute; left: 52px; top: 555px; color: var(--white);
    font-size: 19px; list-style: none;
  }
  .contact__item { display: flex; align-items: flex-start; gap: 12px; line-height: 1.4; }
  .contact__item + .contact__item { margin-top: 4px; }
  .contact__item--address { margin-bottom: 28px; }
  .contact__icon { width: 20px; height: 20px; flex: none; margin-top: 3px; }
</style>
</head>
<body>
<main class="canvas">
  <section class="card card--front" aria-label="Card front">
    <svg class="card__wave" viewBox="0 0 440 770" preserveAspectRatio="none" aria-hidden="true">
      <defs>
        <linearGradient id="wineFill" x1="0" y1="0" x2="0" y2="1">
          <stop offset="0" stop-color="#c24f5b"/>
          <stop offset="1" stop-color="#8a3442"/>
        </linearGradient>
      </defs>
      <path d="M0 360 C120 390 200 360 280 260 C340 190 390 160 440 150 L440 770 L0 770 Z" fill="var(--blush-band)"/>
      <path d="M0 372 C120 402 200 372 280 272 C340 202 390 172 440 162" fill="none" stroke="var(--wine-line)" stroke-width="4"/>
      <path d="M0 382 C120 412 200 382 280 282 C340 212 390 182 440 176 L440 770 L0 770 Z" fill="url(#wineFill)"/>
    </svg>
    <div class="brand"><span class="brand__dot"></span><span>Cedar &amp; Willow<br>Massage Studio</span></div>
    <div class="person">
      <p class="person__name">Mara Ellis</p>
      <p class="person__role">Director</p>
    </div>
    <ul class="contact">
      <li class="contact__item contact__item--address">
        <svg class="contact__icon" viewBox="0 0 20 20" aria-hidden="true"><path d="M10 1a6 6 0 0 0-6 6c0 4.5 6 12 6 12s6-7.5 6-12a6 6 0 0 0-6-6zm0 8.5a2.5 2.5 0 1 1 0-5 2.5 2.5 0 0 1 0 5z" fill="var(--wine-line)"/></svg>
        <span>Dummy city<br>Dummy Country Land</span>
      </li>
      <li class="contact__item">
        <svg class="contact__icon" viewBox="0 0 20 20" aria-hidden="true"><path d="M5 2l3 4-2 2a11 11 0 0 0 6 6l2-2 4 3-2 3C9 18 2 11 2 4z" fill="none" stroke="var(--wine-line)" stroke-width="1.8"/></svg>
        <span>1-555-014-2290</span>
      </li>
      <li class="contact__item">
        <svg class="contact__icon" viewBox="0 0 20 20" aria-hidden="true"><rect x="1" y="4" width="18" height="12" fill="var(--wine-line)"/><path d="M1 4l9 7 9-7" fill="none" stroke="#c24f5b" stroke-width="1.5"/></svg>
        <span>mara@cedarandwillow.com</span>
      </li>
      <li class="contact__item">
        <svg class="contact__icon" viewBox="0 0 20 20" aria-hidden="true"><circle cx="10" cy="10" r="8.5" fill="none" stroke="var(--wine-line)" stroke-width="1.8"/><path d="M1.5 10h17M10 1.5c-4 4.5-4 12.5 0 17M10 1.5c4 4.5 4 12.5 0 17" fill="none" stroke="var(--wine-line)" stroke-width="1.4"/></svg>
        <span>www.cedarandwillow.com</span>
      </li>
    </ul>
  </section>

  <section class="card card--back" aria-label="Card back">
    <div class="brand"><span class="brand__dot"></span><span>Cedar &amp; Willow<br>Massage Studio</span></div>
  </section>
</main>
</body>
</html>
```